HOT TUB - SPAS service needs an business card

I need an business for my company who his specialise in a maintenance,water treatment and cleaning of Hot Tub - Spas for commercial and residential customers. The company operate mainly in the ski resort of Chamonix, Megève and St Gervais. The final product should communicate pure water, cleanest and professional for luxury property's.
I have upload a logo but any improvement on it is welcome.(color,size, details etc..) or any other idea. Thank you
Company Name: 58 BAINS
My name: Lucien Marchetti
Email: lucimarch@examplemail.net
Tel: +33 (0)6 71 58 29 64
Description to be on the card in french(first langage) and in English:
- Spas service
- Entretien, traitement eau, nettoyage.
- Maintenance, water treatment, cleaning.
Industry/Entity Type
Residential
Colors
Designer to choose colors to be used in the design.
Look and feel
Each slider illustrates characteristics of the customer's brand and the style your logo design should communicate.

```html
<!DOCTYPE html>
<html lang="fr">
<head>
<meta charset="utf-8">
<title>58 BAINS – cartes de visite</title>
<link rel="stylesheet" href="https://fonts.googleapis.com/css2?family=Source+Sans+3:wght@400;600;700&display=swap">
<style>
  :root {
    --page: #e9ecef;
    --card-blue: #21a5fd;
    --ink: #ffffff;
    --shadow: rgba(0, 0, 0, 0.18);
  }
  html, body {
    margin: 0;
    padding: 0;
    width: 1200px;
    height: 1127px;
    overflow: hidden;
    background: var(--page);
    font-family: "Source Sans 3", "Myriad Pro", Arial, sans-serif;
    color: var(--ink);
  }
  .stage {
    position: relative;
    width: 1200px;
    height: 1127px;
  }
  .card {
    position: absolute;
    width: 858px;
    height: 490px;
    background: var(--card-blue);
    box-shadow: 0 4px 14px var(--shadow);
  }
  .card--front { left: 51px; top: 51px; }
  .card--back { left: 290px; top: 596px; }

  .brand {
    position: absolute;
    display: flex;
    align-items: center;
    gap: 14px;
    font-weight: 600;
    letter-spacing: 0.5px;
    white-space: nowrap;
  }
  .brand__dot {
    display: inline-block;
    border: 2px solid var(--ink);
    border-radius: 50%;
  }
  .card--front .brand {
    right: 104px;
    top: 100px;
    font-size: 40px;
  }
  .card--front .brand__dot { width: 12px; height: 12px; }

  .contact {
    position: absolute;
    left: 0;
    right: 0;
    top: 262px;
    text-align: center;
  }
  .contact__name {
    margin: 0 0 24px 60px;
    font-size: 36px;
    font-weight: 700;
  }
  .contact__line {
    display: flex;
    justify-content: center;
    align-items: center;
    gap: 12px;
    margin: 0;
    font-size: 31px;
    line-height: 1;
  }
  .contact__phone { margin: 0 0 28px 30px; font-weight: 600; }
  .contact__email { margin-left: 10px; }
  .contact__icon { width: 30px; height: 30px; flex: none; }

  .card--back .brand {
    left: 0;
    right: 0;
    top: 120px;
    justify-content: center;
    font-size: 70px;
  }
  .card--back .brand__dot { width: 20px; height: 20px; }

  .services {
    position: absolute;
    left: 0;
    right: 0;
    top: 280px;
    text-align: center;
  }
  .services__title {
    margin: 0 0 12px;
    font-size: 31px;
    font-weight: 700;
    letter-spacing: 0.3px;
  }
  .services__list {
    margin: 0;
    padding: 0;
    list-style: none;
    font-size: 31px;
    line-height: 42px;
  }
  .services__list span { margin: 0 6px; }
</style>
</head>
<body>
<main class="stage">

  <section class="card card--front" aria-label="Recto de la carte">
    <div class="brand"><span class="brand__dot"></span>58 BAINS</div>
    <div class="contact">
      <p class="contact__name">Lucien Marchetti</p>
      <p class="contact__line contact__phone">
        <svg class="contact__icon" viewBox="0 0 30 30" aria-hidden="true">
          <circle cx="15" cy="15" r="12" fill="none" stroke="#fff" stroke-width="2"/>
          <path d="M10 9c1-1 2-1 3 0l1 2c0 1-1 2-1 2 1 2 2 3 4 4 0 0 1-1 2-1l2 1c1 1 1 2 0 3-2 2-5 1-8-2s-5-6-3-9z" fill="#fff"/>
        </svg>
        +33 (0)6 71 58 29 64
      </p>
      <p class="contact__line contact__email">
        <svg class="contact__icon" viewBox="0 0 30 30" aria-hidden="true">
          <path d="M3 12 15 4l12 8v13H3z" fill="#fff"/>
          <path d="M3 12l12 8 12-8" fill="none" stroke="#21a5fd" stroke-width="2"/>
          <rect x="10" y="9" width="10" height="2" fill="#21a5fd"/>
        </svg>
        lucimarch@examplemail.net
      </p>
    </div>
  </section>

  <section class="card card--back" aria-label="Verso de la carte">
    <div class="brand"><span class="brand__dot"></span>58 BAINS</div>
    <div class="services">
      <p class="services__title">SPAS SERVICES</p>
      <ul class="services__list">
        <li><span>•Entretien</span><span>•traitement eau</span><span>•nettoyage</span></li>
        <li><span>•Maintenance</span><span>•water treatment</span><span>•cleaning.</span></li>
      </ul>
    </div>
  </section>

</main>
</body>
</html>
```